Clear Plastic Card Design

I am looking to have a business card designed from my logo icon. I am looking to match the style of a different business card I have attached in the files.
Looking for a card that is plastic, with layers of transparency in the shape of my logo icon (also attached in the files) - not a circle like the other card. The winning design will incorporate the red icon logo on the front and back and include the charity's name, "Light for the Weary Souls" in the same or similar font, as well as an email and phone number. For now, use the email: email@lightfortheweary-mail.org and the phone number 555-382-7194.
We like how the sample business card has transparency, partial and full opacity layers and a matching color scheme. Files will need to be in vector so that our business card printing company can work with it.
UPDATE:
We've some excellent designs in, thank you everyone! I got an early review from the owner, and he requested a minor redirect to find his perfect design. He wants the design to stand out by NOT being a rectangle. Try instead a circle, square, or best yet - something that falls in the outline of the logo icon, either fully or partially. Thank you, everyone!
Light for the Weary Souls text should be incorporated as well as a phone and email.

```html
<!DOCTYPE html>
<html lang="en">
<head>
<meta charset="UTF-8">
<title>Light for the Weary Souls – Round Card</title>
<link rel="stylesheet" href="https://fonts.googleapis.com/css2?family=Questrial&family=Roboto:wght@400;700&display=swap">
<style>
  :root {
    --page-bg: #ececec;
    --card-bg: #ffffff;
    --band-orange: #f26a1b;
    --band-red: #e0201f;
    --band-deep: #c8141c;
    --ink: #1d1d1d;
    --accent: #e3153c;
    --white: #ffffff;
  }
  * { box-sizing: border-box; margin: 0; padding: 0; }
  html, body {
    width: 1175px;
    height: 1200px;
    overflow: hidden;
    background: var(--page-bg);
  }
  .canvas {
    position: relative;
    width: 1175px;
    height: 1200px;
  }
  .card {
    position: absolute;
    left: 225px;
    top: 237px;
    width: 724px;
    height: 724px;
    border-radius: 50%;
    background: var(--card-bg);
    overflow: hidden;
  }
  .band {
    position: absolute;
    left: 0;
    width: 100%;
    display: flex;
    align-items: center;
    justify-content: center;
    color: var(--white);
    font-family: "Roboto", Arial, sans-serif;
  }
  .band--top {
    top: 76px;
    height: 58px;
    background: linear-gradient(100deg, var(--band-red) 0%, var(--band-orange) 45%, var(--band-red) 100%);
  }
  .band--bottom {
    top: 585px;
    height: 62px;
    background: linear-gradient(100deg, var(--band-deep) 0%, var(--band-red) 50%, var(--band-orange) 100%);
  }
  .phone {
    display: flex;
    align-items: center;
    gap: 10px;
    font-size: 36px;
    font-weight: 700;
    letter-spacing: 0.5px;
  }
  .phone__icon { width: 30px; height: 30px; }
  .email {
    font-size: 24px;
    font-weight: 400;
  }
  .brand {
    position: absolute;
    left: 124px;
    top: 290px;
    display: flex;
    align-items: flex-end;
    gap: 34px;
  }
  .brand__name {
    font-family: "Questrial", Arial, sans-serif;
    font-size: 36px;
    line-height: 1.22;
    color: var(--ink);
    padding-bottom: 8px;
  }
  .brand__mark {
    width: 150px;
    height: 150px;
    border-radius: 50%;
    background: var(--accent);
  }
  .website {
    position: absolute;
    left: 0;
    top: 510px;
    width: 100%;
    text-align: center;
    font-family: "Roboto", Arial, sans-serif;
    font-size: 23px;
    font-weight: 700;
    color: var(--ink);
  }
  .website__domain { color: var(--accent); }
</style>
</head>
<body>
<main class="canvas">
  <section class="card">
    <div class="band band--top" role="img" aria-label="Band of faceted orange and red geometric pattern">
      <p class="phone">
        <svg class="phone__icon" viewBox="0 0 24 24" aria-hidden="true">
          <path fill="#ffffff" d="M6.6 10.8a15.1 15.1 0 0 0 6.6 6.6l2.2-2.2a1 1 0 0 1 1-.25 11.4 11.4 0 0 0 3.6.57 1 1 0 0 1 1 1V20a1 1 0 0 1-1 1A17 17 0 0 1 3 4a1 1 0 0 1 1-1h3.5a1 1 0 0 1 1 1c0 1.25.2 2.45.57 3.6a1 1 0 0 1-.25 1z"/>
        </svg>
        555-382-7194
      </p>
    </div>

    <div class="brand">
      <p class="brand__name">Light for the<br>Weary Souls</p>
      <div class="brand__mark" aria-hidden="true"></div>
    </div>

    <p class="website">www.<span class="website__domain">lightfortheweary-souls</span>.org</p>

    <div class="band band--bottom" role="img" aria-label="Band of faceted red and orange geometric pattern">
      <p class="email">email@lightfortheweary-mail.org</p>
    </div>
  </section>
</main>
</body>
</html>
```